design an extra page for our profile

we are looking for someone to create another page like the attached but with the below changes:
heading changed to (Construction)
icons changed and names to reflect new services i.e
- Residential Building
- Commercial Building
- Landscaping
- Concrete
- Painting

the very bottom of the page is to stay the same with our office info

```html
<!DOCTYPE html>
<html lang="en">
<head>
<meta charset="utf-8">
<title>Construction Services</title>
<link href="https://fonts.googleapis.com/css2?family=Montserrat:wght@300;400;500;600;700&display=swap" rel="stylesheet">
<style>
  :root {
    --canvas: #cacaca;
    --brand-blue: #223e93;
    --white: #ffffff;
    --photo-light: #eef2fa;
    --photo-mid: #c9d1e0;
    --photo-dark: #8a93a6;
  }
  * { margin: 0; padding: 0; box-sizing: border-box; }
  html, body { width: 1200px; height: 1000px; overflow: hidden; }
  body {
    background: var(--canvas);
    font-family: "Montserrat", sans-serif;
    position: relative;
  }
  .flyer {
    position: absolute;
    left: 308px; top: 122px;
    width: 584px; height: 756px;
    background: var(--white);
    overflow: hidden;
  }
  .backdrop-photo {
    position: absolute;
    left: 0; top: 144px; width: 584px; height: 550px;
    background: linear-gradient(160deg, var(--photo-mid) 0%, var(--photo-light) 35%, var(--photo-light) 60%, var(--photo-mid) 100%);
  }
  .header-photo {
    position: absolute;
    left: 0; top: 0; width: 584px; height: 144px;
    background: linear-gradient(180deg, #7d8ba3 0%, #a9a6a4 55%, #4b4d52 100%);
  }
  .header-band {
    position: absolute; left: 0; top: 0;
    width: 584px; height: 144px;
  }
  .title {
    position: absolute; left: 10px; top: 42px;
    color: var(--white);
  }
  .title-main {
    font-weight: 700; font-size: 21px; letter-spacing: 0.3px;
    padding-bottom: 4px; width: 230px;
    border-bottom: 1px solid var(--white);
  }
  .title-sub {
    font-weight: 300; font-size: 18px; letter-spacing: 0.5px; margin-top: 3px;
  }
  .intro {
    position: absolute; left: 0; top: 205px; width: 600px;
    text-align: center; color: var(--brand-blue);
    font-size: 11.5px; font-weight: 400; line-height: 21px; letter-spacing: 0.2px;
  }
  .offer {
    position: absolute; left: 0; top: 266px; width: 600px;
    text-align: center; color: var(--brand-blue);
    font-size: 13.5px; font-weight: 600;
  }
  .service {
    position: absolute; width: 127px; height: 109px;
    background: var(--brand-blue); color: var(--white);
    text-align: center;
  }
  .service svg {
    position: absolute; left: 33px; top: 16px; width: 60px; height: 60px;
    fill: none; stroke: var(--white); stroke-width: 2; stroke-linejoin: round; stroke-linecap: round;
  }
  .service-name {
    position: absolute; left: 0; right: 0; top: 85px;
    font-size: 7.5px; font-weight: 700; letter-spacing: 0.1px;
  }
  .footer {
    position: absolute; left: 0; top: 694px; width: 584px; height: 62px;
    background: var(--brand-blue); color: var(--white);
  }
  .footer-brand {
    position: absolute; left: 28px; top: 22px;
    font-size: 16px; font-weight: 700; letter-spacing: 0.5px;
  }
  .footer-office {
    position: absolute; left: 138px; top: 19px; width: 408px;
    font-size: 11.5px; font-weight: 500;
    padding-bottom: 4px; border-bottom: 1px solid var(--white);
  }
  .footer-office strong { font-weight: 700; }
  .footer-web {
    position: absolute; left: 138px; top: 42px;
    font-size: 9.5px; font-weight: 500; letter-spacing: 0.2px;
  }
  .footer-web strong { font-weight: 700; }
</style>
</head>
<body>
<main class="flyer">
  <div class="backdrop-photo" role="img" aria-label="Upward view of a glass skyscraper with a tower crane, faded in pale blue"></div>
  <div class="header-photo" role="img" aria-label="Red safety hard hat resting on asphalt at a construction site"></div>
  <svg class="header-band" viewBox="0 0 584 144" aria-hidden="true">
    <polygon points="0,0 284,0 347,144 0,144" fill="var(--brand-blue)"/>
  </svg>

  <header class="title">
    <h1 class="title-main">CONSTRUCTION</h1>
    <p class="title-sub">SERVICES</p>
  </header>

  <p class="intro">AS A NEW TENANTS TO THE BUILDING AND AS A WAY<br>OF INTRODUCING OURSELVES WE WOULD LIKE TO OFFER</p>
  <p class="offer">A 10% DISCOUNT ON ANY &nbsp;OF THE BELOW SERVICES</p>

  <div class="service" style="left:36px;top:340px">
    <svg viewBox="0 0 60 60"><path d="M6 28 L22 12 L38 28 M10 24 V54 H52 V36 M30 40 L42 28 L56 40 M34 36 V54 M42 44 h6 v10 M16 20 h6 v6 h-6z M14 8 v6 M20 8 h-8"/></svg>
    <span class="service-name">RESIDENTIAL BUILDING</span>
  </div>
  <div class="service" style="left:228px;top:340px">
    <svg viewBox="0 0 60 60"><path d="M6 56 H54 M12 56 V14 H28 V56 M34 56 V10 H50 V56 M28 30 H34 M16 20 h8 M16 28 h8 M16 36 h8 M16 44 h8 M38 16 h8 M38 24 h8 M38 32 h8 M38 40 h8 M20 14 v-6 M42 10 v-6"/></svg>
    <span class="service-name">COMMERCIAL BUILDING</span>
  </div>
  <div class="service" style="left:421px;top:340px">
    <svg viewBox="0 0 60 60"><path d="M4 40 Q30 26 56 34 M4 52 Q24 38 48 56 M20 50 Q34 40 56 46 M44 30 V18 M44 4 C38 8 38 20 44 22 C50 20 50 8 44 4 M10 30 V22 M10 22 a4 4 0 1 1 0.1 0 M24 32 V26 h10 v6 M22 27 L29 21 L36 27"/></svg>
    <span class="service-name">LANDSCAPING</span>
  </div>
  <div class="service" style="left:124px;top:489px">
    <svg viewBox="0 0 60 60"><path d="M4 44 V28 L30 16 L36 26 V44 Z M36 44 V24 H48 L56 34 V44 Z M42 28 h5 l4 6 h-9z M10 26 L28 18 M10 36 L32 26"/><circle cx="14" cy="48" r="4"/><circle cx="44" cy="48" r="4"/></svg>
    <span class="service-name">CONCRETE</span>
  </div>
  <div class="service" style="left:331px;top:489px">
    <svg viewBox="0 0 60 60"><path d="M10 6 H50 V16 H10 Z M50 11 H56 V24 H30 V32 M26 32 h8 v10 h-8z M28 42 h4 v14 h-4z M10 16 v6 M16 16 v10"/></svg>
    <span class="service-name">PAINTING</span>
  </div>

  <footer class="footer">
    <span class="footer-brand">KORA</span>
    <p class="footer-office"><strong>HOME OFFICE:</strong> 1300 00 4821 .&nbsp; Suite 2.04 , 12 Meridian Drive Oakvale</p>
    <p class="footer-web"><strong>www.KORA-SERVICES.COM.AU</strong>&nbsp; SYDNEY | CANBERRA | BRISBANE | MELBOURNE</p>
  </footer>
</main>
</body>
</html>
```